Tidal Forge - Crypto Currency Miner Powered by Renewable Energy Website

We Need Web Pages Design for Website for Crypto Currency Miner

Serivices include:
Mining Rig Sales
Housing for Rigs turnkey on renewable energy grid
Cloud Mining term packages
Updates

http://www.vaultrigsurvey.example (Competitors sites)

Target Market(s)

Investers for Mining Rigs and terms for 1,2 or 3 years of Hash rate

Industry/Entity Type

Mining

Number of Pages Required

5+ page

Font styles to use
Sans Serif

Colors
add136
9bcb3c
606060
474747
ffc214
cadf82
fbee3e
876aae
6b449b

Requirements
Must have
• Pictures of Solar, Wind and power Factor Correction units
Nice to have
• e-commerce platform so contract terms can be purchased through website
Should not have
• Heavy construction equipment

```html
<!DOCTYPE html>
<html lang="en">
<head>
<meta charset="utf-8">
<title>Tidal Forge – Renewable Crypto Mining</title>
<link href="https://fonts.googleapis.com/css2?family=Roboto+Condensed:wght@300;400;700&display=swap" rel="stylesheet">
<style>
:root{
  --green:#9bcb3c;
  --green-bright:#add136;
  --green-pale:#cadf82;
  --charcoal:#474747;
  --grey:#606060;
  --amber:#ffc214;
  --lemon:#fbee3e;
  --navy:#232383;
  --navy-deep:#17176a;
  --row-tint:#ffe08f;
  --white:#ffffff;
  --backdrop:#ebebeb;
}
*{margin:0;padding:0;box-sizing:border-box}
html,body{width:1200px;height:1200px;overflow:hidden;background:var(--backdrop)}
body{font-family:"Roboto Condensed",sans-serif}
.stage{position:absolute;left:0;top:0;width:1500px;height:1500px;transform:scale(.8);transform-origin:0 0}
.page{position:absolute;left:403px;top:0;width:693px;height:1440px;overflow:hidden;background:var(--charcoal)}
.bands{position:absolute;left:0;top:0}
.abs{position:absolute}
.fine{font-size:7.4px;line-height:9.4px;font-weight:300;text-align:justify}
.lead{font-size:10.5px;line-height:12.6px;font-weight:300;text-align:justify}
.light{color:var(--white)}
.dark{color:var(--charcoal)}
.btn{position:absolute;width:72px;height:16px;border:1px solid var(--white);border-radius:2px;font-size:8px;line-height:14px;text-align:center;color:var(--white)}
.btn.green{border-color:var(--green);color:var(--green)}
.btn.on-amber{border-color:var(--white);color:var(--white)}
.heading{position:absolute;font-size:23px;font-weight:400;letter-spacing:-.3px;white-space:nowrap}
.heading .accent{color:var(--green)}
.rule{position:absolute;height:2px}
.tablet{position:absolute;left:345px;top:-20px;width:300px;height:130px;border-radius:18px;transform:rotate(-9deg);background:#1c1c1c;padding:10px}
.tablet .screen{width:100%;height:100%;border-radius:8px;background:linear-gradient(160deg,#7fb3e6,#2f6cb5 60%,#d9e8f5)}
.tile{position:absolute;width:96px;height:96px;border-radius:6px;text-align:center;font-size:13px;line-height:14px;letter-spacing:-.2px}
.tile svg{display:block;margin:12px auto 4px}
.tile.safe{background:var(--green);color:var(--white)}
.tile.app{background:var(--amber);color:var(--white)}
.tile.wallet{background:var(--lemon);color:var(--charcoal)}
.tile.cover{background:var(--white);color:var(--charcoal)}
.solar{position:absolute;left:318px;top:545px;width:336px;height:275px;background:radial-gradient(ellipse at 55% 40%,#3b5eb5 0,#2a4690 45%,#e8ecf3 72%,rgba(255,255,255,0) 80%)}
.pricing{position:absolute;left:111px;top:899px;width:305px;border-collapse:separate;border-spacing:2px 0;font-size:6.2px;color:#7a7a7a}
.pricing td{height:20px;text-align:center;padding:0}
.pricing td.label{text-align:left;padding-left:5px;color:var(--charcoal);width:75px}
.pricing tr.alt td{background:var(--row-tint)}
.pricing tr.plain td{background:var(--white)}
.pricing tr.gap td{height:8px;background:transparent}
.plan{height:60px;vertical-align:top;color:var(--white)}
.plan .name{display:block;height:21px;line-height:21px;font-size:10px}
.plan .price{display:block;height:39px;font-size:15px;line-height:30px;position:relative}
.plan .per{position:absolute;left:0;right:0;top:27px;font-size:3.6px;line-height:5px}
.tarif .name,.tarif .price{background:var(--lemon);color:var(--charcoal)}
.tarif .price{font-size:7.5px;line-height:26px}
.start .name{background:var(--green)}.start .price{background:#8fbd34}
.basic .name{background:var(--charcoal)}.basic .price{background:#8b8b8b}
.premium .name{background:var(--navy)}.premium .price{background:var(--navy-deep)}
.mark{font-size:9px;color:var(--grey)}
.footer-title{position:absolute;font-size:14px;font-weight:300;color:var(--amber)}
.footer-title.follow{color:var(--green)}
.footer-text{position:absolute;font-size:8px;line-height:11px;color:var(--white);font-weight:300}
.ghost{position:absolute;width:88px;height:18px;border:1px solid var(--amber);font-size:8px;line-height:16px;text-align:center;color:var(--amber)}
.social{position:absolute;left:250px;top:1334px;width:80px;display:flex;flex-wrap:wrap;gap:6px 8px}
.social span{width:19px;height:19px;border:1.4px solid var(--white);border-radius:50%}
.nav{position:absolute;top:1316px;font-size:8px;line-height:19px;color:var(--white);font-weight:300}
</style>
</head>
<body>
<div class="stage">
<main class="page">
  <svg class="bands" width="693" height="1440" viewBox="0 0 693 1440" aria-hidden="true">
    <polygon points="0,0 693,0 693,78 0,187" fill="var(--green)"/>
    <polygon points="0,540 693,433 693,787 0,895" fill="var(--white)"/>
    <polygon points="0,895 693,787 693,1140 0,1250" fill="var(--amber)"/>
  </svg>

  <!-- Intro band -->
  <p class="abs fine light" style="left:112px;top:0;width:200px">tio nihil pariatur.</p>
  <p class="abs fine light" style="left:112px;top:20px;width:200px">Lorem ipsum dolor sit amet, consectetur adipisicing elit. Quam earum, provident ad, porro aperiam dolore, blanditiis, nihil pariatur eius adipisci consequuntur officiis. Excepturi, nostrum? Id incidunt nescius officia hic distinctio nihil pariatur. Lorem ipsum dolor sit amet, consectetur adipisicing elit. Quam earum, provident ad, porro aperiam dolore, blanditiis, nihil pariatur eius adipisci consequuntur officiis. Excepturi, nostrum? Id incidunt nescius officia hic distinctio nihil pariatur.</p>
  <span class="btn" style="left:239px;top:97px">Learn More</span>
  <div class="tablet" role="img" aria-label="Tablet showing the globe wrapped in clouds"><div class="screen"></div></div>

  <!-- Why choose -->
  <div class="tile safe" style="left:120px;top:215px">
    <svg width="42" height="48" viewBox="0 0 42 48" fill="none" stroke="#fff" stroke-width="2"><path d="M21 3 L37 9 V22 C37 33 30 41 21 45 C12 41 5 33 5 22 V9 Z"/><path d="M21 9 L31 13 V22 C31 29 27 34 21 37 C15 34 11 29 11 22 V13 Z"/><circle cx="21" cy="21" r="4"/><path d="M19 25 L18 31 H24 L23 25"/></svg>
    Safe And Secure</div>
  <div class="tile app" style="left:239px;top:215px">
    <svg width="46" height="48" viewBox="0 0 46 48" fill="none" stroke="#fff" stroke-width="2"><rect x="4" y="4" width="22" height="40" rx="3"/><path d="M4 10 H26 M4 38 H26"/><circle cx="16" cy="22" r="5"/><circle cx="33" cy="28" r="6"/><circle cx="33" cy="28" r="2"/><path d="M16 14 V17 M16 27 V30 M8 22 H11 M21 22 H24"/></svg>
    Mobile App</div>
  <div class="tile wallet" style="left:120px;top:328px">
    <svg width="46" height="48" viewBox="0 0 46 48" fill="none" stroke="#474747" stroke-width="2"><path d="M10 12 H34 V6 H10 Z M8 14 H38 V40 H8 Z"/><rect x="28" y="22" width="12" height="10" rx="2"/><circle cx="33" cy="27" r="1.5"/><path d="M6 26 L14 23 L22 26 V32 C22 36 18 39 14 41 C10 39 6 36 6 32 Z" fill="#fbee3e"/><path d="M10 32 L13 35 L18 29"/></svg>
    Secure Wallet</div>
  <div class="tile cover" style="left:239px;top:328px">
    <svg width="46" height="44" viewBox="0 0 46 44" fill="none" stroke="#474747" stroke-width="2"><rect x="6" y="6" width="26" height="34" rx="2"/><rect x="13" y="3" width="12" height="6" rx="1"/><path d="M19 14 L27 17 V23 C27 28 23 31 19 33 C15 31 11 28 11 23 V17 Z"/><path d="M15 23 L18 26 L23 20"/><circle cx="35" cy="32" r="7" fill="#fff"/><path d="M35 28 V36 M31 32 H39"/></svg>
    Covered By<br>Insurance</div>

  <h2 class="heading light" style="right:104px;top:172px">Why Choose <span class="accent">Tidal Forge</span>?</h2>
  <div class="rule" style="left:381px;top:202px;width:208px;background:var(--grey)"></div>
  <div class="rule" style="left:484px;top:202px;width:105px;background:var(--green)"></div>
  <p class="abs lead light" style="left:388px;top:220px;width:201px">Lorem ipsum dolor sit amet, consectetur adipisicing elit. Aliquam praesentium, distinctio dicta molestias dignissimos.</p>
  <p class="abs fine light" style="left:388px;top:270px;width:201px">Lorem ipsum dolor sit amet, consectetur adipisicing elit. Quam earum, provident ad, porro aperiam dolore, blanditiis, nihil pariatur eius adipisci consequuntur officiis. Excepturi, nostrum? Id incidunt nescius officia hic distinctio nihil pariatur.</p>
  <p class="abs fine light" style="left:388px;top:317px;width:201px">Lorem ipsum dolor sit amet, consectetur adipisicing elit. Quam earum, provident ad, porro aperiam dolore, blanditiis, nihil pariatur eius adipisci consequuntur officiis. Excepturi, nostrum? Id incidunt nescius officia hic distinctio nihil pariatur. Lorem ipsum dolor sit amet, consectetur adipisicing elit. Quam earum, provident ad, porro aperiam dolore, blanditiis, nihil pariatur eius adipisci consequuntur officiis. Excepturi, nostrum? Id incidunt nescius officia hic distinctio nihil pariatur.</p>
  <span class="btn" style="left:515px;top:394px">Learn More</span>

  <!-- About -->
  <h2 class="heading dark" style="left:105px;top:561px">About <span class="accent">Tidal Forge</span>?</h2>
  <div class="rule" style="left:105px;top:591px;width:150px;background:var(--grey)"></div>
  <div class="rule" style="left:158px;top:591px;width:97px;background:var(--green)"></div>
  <p class="abs lead dark" style="left:112px;top:608px;width:200px">Lorem ipsum dolor sit amet, consectetur adipisicing elit. Aliquam praesentium, distinctio dicta molestias dignissimos.</p>
  <p class="abs fine dark" style="left:112px;top:659px;width:200px">Lorem ipsum dolor sit amet, consectetur adipisicing elit. Quam earum, provident ad, porro aperiam dolore, blanditiis, nihil pariatur eius adipisci consequuntur officiis. Excepturi, nostrum? Id incidunt nescius officia hic distinctio nihil pariatur.</p>
  <p class="abs fine dark" style="left:112px;top:706px;width:200px">Lorem ipsum dolor sit amet, consectetur adipisicing elit. Quam earum, provident ad, porro aperiam dolore, blanditiis, nihil pariatur eius adipisci consequuntur officiis. Excepturi, nostrum? Id incidunt nescius officia hic distinctio nihil pariatur. Lorem ipsum dolor sit amet, consectetur adipisicing elit. Quam earum, provident ad, porro aperiam dolore, blanditiis, nihil pariatur eius adipisci consequuntur officiis. Excepturi, nostrum? Id incidunt nescius officia hic distinctio nihil pariatur.</p>
  <span class="btn green" style="left:239px;top:782px">Learn More</span>
  <div class="solar" role="img" aria-label="Solar panel on a steel pole"></div>

  <!-- Prices -->
  <table class="pricing">
    <tr>
      <td class="plan tarif"><span class="name">TARIF</span><span class="price">PRICING TABLE<span class="per">LOREM IPSUM DOLOR SIT AMET, CONSECTETUR</span></span></td>
      <td class="plan start"><span class="name">START</span><span class="price">$29.99<span class="per">PER MONTH</span></span></td>
      <td class="plan basic"><span class="name">BASIC</span><span class="price">$49.99<span class="per">PER MONTH</span></span></td>
      <td class="plan premium"><span class="name">PREMIUM</span><span class="price">$69.99<span class="per">PER MONTH</span></span></td>
    </tr>
    <tr class="gap"><td></td><td></td><td></td><td></td></tr>
    <tr class="plain"><td class="label">Consectetur adipiscing</td><td class="mark">✕</td><td class="mark">✓</td><td class="mark">✓</td></tr>
    <tr class="alt"><td class="label">Adipiscing consectetur</td><td>4 GB</td><td>16 GB</td><td>UNLIMITED</td></tr>
    <tr class="plain"><td class="label">Pellentesque</td><td>15 CONTACTS</td><td>30 CONTACTS</td><td>&gt;50 CONTACTS</td></tr>
    <tr class="alt"><td class="label">Vitae purus</td><td class="mark">✓</td><td class="mark">✓</td><td class="mark">✓</td></tr>
    <tr class="plain"><td class="label">Donec egestas nec</td><td class="mark">✕</td><td class="mark">✕</td><td class="mark">✓</td></tr>
    <tr class="alt"><td class="label">Mauris interdum</td><td class="mark">✓</td><td class="mark">✓</td><td class="mark">✓</td></tr>
    <tr class="plain"><td class="label">Iacus in nisi molestie</td><td>1 PERSON</td><td>4 PERSON</td><td>&gt;10 PERSON</td></tr>
    <tr class="alt"><td class="label">Iacus in nisi molestie</td><td class="mark">✕</td><td class="mark">✓</td><td class="mark">✓</td></tr>
    <tr class="plain"><td class="label">Mauris ultrices</td><td class="mark">✓</td><td class="mark">✓</td><td class="mark">✓</td></tr>
    <tr class="alt"><td class="label">Pellentesque</td><td>4 GB</td><td>16 GB</td><td>UNLIMITED</td></tr>
  </table>

  <h2 class="heading dark" style="left:442px;top:909px">Prices</h2>
  <div class="rule" style="left:482px;top:941px;width:100px;background:var(--charcoal)"></div>
  <p class="abs lead dark" style="left:442px;top:952px;width:147px;font-weight:400">Lorem ipsum dolor sit amet, consectetur adipisicing elit. Aliquam praesentium, distinctio dicta molestias d</p>
  <p class="abs fine dark" style="left:442px;top:999px;width:147px">Lorem ipsum dolor sit amet, consectetur adipisicing elit. Quam earum, provident ad, porro aperiam dolore, blanditiis, nihil pariatur eius adipisci consequuntur officiis. Excepturi, nostrum? Id incidunt nescius officia hic distinctio nihil pariatur.</p>
  <span class="btn on-amber" style="left:515px;top:1059px">Learn More</span>

  <!-- Footer -->
  <h3 class="footer-title" style="left:111px;top:1256px">Member Area</h3>
  <p class="footer-text" style="left:111px;top:1286px">If you don't have an account,<br>sign up for free.</p>
  <span class="ghost" style="left:112px;top:1325px">SIGN UP</span>
  <span class="ghost" style="left:112px;top:1360px">LOGIN</span>

  <h3 class="footer-title follow" style="left:249px;top:1256px">Follow us</h3>
  <p class="footer-text" style="left:249px;top:1286px">Stay up to date with<br>Tidal Forge activities.</p>
  <div class="social" aria-label="Social links"><span></span><span></span><span></span><span></span><span></span><span></span></div>

  <nav class="nav" style="left:375px">HOME<br>PRICING<br>OUR OFFER</nav>
  <nav class="nav" style="left:450px">ABOUT US<br>DATACENTER<br>PRESS</nav>
  <nav class="nav" style="left:531px">PRIVACY<br>CONTACT</nav>
</main>
</div>
</body>
</html>
```